Business card for Sports Apparel business

DOUBLE SIDED DESIGN
We need business cards for a new sports apparel business. We are developing a protective headband for soccer initially.
Torvalle is focused on designing and developing head protection products to reduce the likelihood of concussion when playing sports. Exploring and understanding medical insights, material science research, current and former players experiences and governing bodies guidelines has allowed Torvalle to develop the safety, style, form and function requirements of a suitable product to bring to market.
Target Market(s)
Mums buying kits for the sons and daughters. Amateur footballers.
Industry/Entity Type
Sporting Good
Contact Information for Business Card
Martin Ashworth - CEO
Mobile: +44 7431589027
Email: martin@torvalle.co.uk
Tel: 0208 5519372
Helena Pargeter - COO
Mob: +44 7385 640117
Email: helena@torvalle.co.uk
Tel: 0208 5519372
Duncan Farrow - CCO
Mob: +44 7564 293081
Email: duncan@torvalle.co.uk
Tel: 0208 5519372
Look and feel
Each slider illustrates characteristics of the customer's brand and the style your logo design should communicate.

```html
<!DOCTYPE html>
<html lang="en">
<head>
<meta charset="utf-8">
<title>Torvalle Business Card</title>
<link href="https://fonts.googleapis.com/css2?family=Montserrat:wght@400;500;700&display=swap" rel="stylesheet">
<style>
  :root {
    --stage: #2b2522;
    --card: #1b1b1c;
    --edge: #1d6ea8;
    --accent: #1f7fc4;
    --ink: #f2f2f2;
  }
  * { margin: 0; padding: 0; box-sizing: border-box; }
  html, body { width: 1200px; height: 716px; overflow: hidden; }
  body {
    background: var(--stage);
    font-family: "Montserrat", sans-serif;
    position: relative;
  }
  .card {
    position: absolute;
    top: 193px;
    width: 520px;
    height: 330px;
    background: var(--card);
    border-radius: 8px;
    box-shadow: 0 10px 28px rgba(0,0,0,.45);
  }
  .card--front { left: 50px; border-bottom: 4px solid var(--edge); }
  .card--back { left: 630px; }

  .wordmark {
    display: flex;
    align-items: center;
    gap: 12px;
    color: var(--ink);
    font-weight: 700;
    letter-spacing: 2px;
    text-transform: uppercase;
  }
  .wordmark__square {
    background: var(--accent);
    display: block;
  }
  .card--front .wordmark {
    position: absolute;
    left: 50%;
    top: 50%;
    transform: translate(-50%, -50%);
    font-size: 40px;
  }
  .card--front .wordmark__square { width: 22px; height: 22px; }

  .card--back .wordmark {
    position: absolute;
    left: 44px;
    top: 40px;
    font-size: 26px;
  }
  .card--back .wordmark__square { width: 14px; height: 14px; }

  .person {
    position: absolute;
    left: 44px;
    top: 186px;
  }
  .person__name {
    color: var(--accent);
    font-size: 15px;
    font-weight: 500;
    text-transform: uppercase;
    letter-spacing: .5px;
  }
  .person__role {
    color: var(--ink);
    font-size: 11px;
    margin-top: 3px;
  }
  .person__rule {
    width: 18px;
    height: 1px;
    background: var(--accent);
    margin-top: 10px;
  }
  .contact {
    position: absolute;
    left: 44px;
    right: 24px;
    top: 244px;
    color: var(--ink);
    font-size: 10.5px;
    white-space: nowrap;
  }
  .contact__label { color: var(--accent); font-weight: 500; }
</style>
</head>
<body>
  <section class="card card--front" aria-label="Card front">
    <div class="wordmark"><span class="wordmark__square"></span>Torvalle</div>
  </section>

  <section class="card card--back" aria-label="Card back">
    <div class="wordmark"><span class="wordmark__square"></span>Torvalle</div>
    <div class="person">
      <p class="person__name">Martin Ashworth</p>
      <p class="person__role">CEO</p>
      <div class="person__rule"></div>
    </div>
    <p class="contact">
      <span class="contact__label">P:</span> 0208 5519372 |
      <span class="contact__label">M:</span> +44 7431589027 |
      <span class="contact__label">E:</span> martin@torvalle.co.uk
    </p>
  </section>
</body>
</html>
```